Musical download and streaming website

hello designers, I want to start up a musical website where users can download and rate music of different genres such as RnB, Hip hop, rock, afro-pop. This website should be attractive and contemporary. There will be a search column for different songs. Music files will be mp3, mwa, and others. I like blue, gold, pink and indigo colors. My website should resemble http://tunovalt.com. There should be good imaginary of music stars on my website.

```html
<!DOCTYPE html>
<html lang="en">
<head>
<meta charset="utf-8">
<title>Velora Music</title>
<link rel="stylesheet" href="https://fonts.googleapis.com/css2?family=Lato:wght@300;400;700&family=Roboto:wght@400;500;700&family=Dancing+Script:wght@700&display=swap">
<style>
:root{
  --indigo:#5a2ca0;
  --indigo-dark:#3f1d7a;
  --pink:#e0136d;
  --blue:#2a98d8;
  --orange:#f08a1c;
  --gold:#f3a325;
  --paper:#ffffff;
  --mist:#eeeeee;
  --line:#d6d6d6;
  --ink:#222222;
  --muted:#666666;
  --footer:#1c1c1c;
  --footer-text:#b8b8b8;
}
*{box-sizing:border-box;margin:0;padding:0}
html,body{width:668px;height:1200px;overflow:hidden}
body{position:relative;background:var(--mist);font-family:"Roboto",Arial,sans-serif;color:var(--ink)}
.abs{position:absolute}

/* header */
.site-header{left:0;top:0;width:668px;height:58px;background:var(--mist)}
.brand{left:42px;top:12px;color:var(--indigo);font-family:"Lato",sans-serif;font-weight:700;line-height:1}
.brand .name{font-size:19px;letter-spacing:1px;display:block}
.brand .sub{font-size:9px;letter-spacing:5px;display:block;margin-top:3px;padding-left:16px}
.search-field{left:402px;top:12px;width:166px;height:18px;background:var(--paper);border-radius:9px 0 0 9px;font-size:6.5px;font-style:italic;color:#aaa;padding:6px 0 0 12px}
.search-btn{left:562px;top:12px;width:63px;height:18px;background:var(--indigo);border-radius:9px;color:#fff;font-size:7px;font-weight:500;text-align:center;line-height:18px}
.filters{left:406px;top:39px;display:flex;gap:14px;font-size:7px;color:#555}
.filters span{display:flex;align-items:center;gap:4px}
.radio{width:7px;height:7px;border:1px solid #999;border-radius:50%;display:inline-block;position:relative}
.radio.on::after{content:"";position:absolute;left:1px;top:1px;width:3px;height:3px;border-radius:50%;background:var(--indigo)}

/* hero */
.hero{left:0;top:58px;width:668px;height:308px;background:radial-gradient(ellipse at 50% 70%,#b25a2c 0%,#8a6b66 22%,#6f7d8c 45%,#5e6c7b 100%)}
.hero-arrow{top:186px}
.hero-caption{left:161px;top:232px;width:350px;height:37px;background:rgba(60,60,60,.55);color:#fff;font-family:"Dancing Script",cursive;font-size:30px;text-align:center;line-height:37px;white-space:nowrap}

/* features */
.features{left:0;top:366px;width:668px;height:231px;background:var(--paper)}
.feature{top:30px;width:175px}
.feature .badge{width:70px;height:70px;border-radius:50%;display:flex;align-items:center;justify-content:center}
.feature h3{margin-top:10px;font-family:"Lato",sans-serif;font-weight:300;font-size:13px;line-height:15px;color:#222}
.feature h3 b{font-weight:700;display:block}
.feature p{margin-top:9px;font-family:Arial,sans-serif;font-size:7px;line-height:11px;color:var(--muted)}
.pill{display:inline-block;margin-top:12px;width:61px;height:19px;border-radius:10px;color:#fff;font-size:6.5px;font-weight:700;text-align:center;line-height:19px}
.pink{background:var(--pink)}.blue{background:var(--blue)}.orange{background:var(--orange)}

/* popular */
.popular-title{left:42px;top:628px;font-family:"Lato",sans-serif;font-size:16px;font-weight:300;color:#222}
.popular-title b{font-weight:700}
.tabs{left:42px;top:654px;width:585px;border-bottom:1px solid var(--line);height:28px;display:flex;font-size:9px;color:#888}
.tabs span{padding:10px 0 0}
.tabs .sep{padding:10px 10px 0;color:#999}
.tabs .active{color:var(--indigo);border-bottom:2px solid var(--indigo);padding:10px 8px 0;margin-bottom:-1px}
.card{width:185px;height:84px;border:1px solid var(--line);background:var(--mist)}
.cover{left:10px;top:12px;width:46px;height:46px}
.card h4{left:70px;top:13px;font-size:7.5px;font-weight:500;color:var(--indigo);display:flex;gap:7px}
.stars{color:var(--gold);letter-spacing:0}
.card p{left:70px;top:28px;width:108px;font-size:7px;line-height:10px;color:#555}
.dl{left:67px;top:57px;width:73px;height:17px;border-radius:9px;background:var(--indigo);color:#fff;font-size:6.5px;font-weight:700;display:flex;align-items:center;justify-content:center;gap:4px}
.view-all{left:275px;top:903px;width:119px;height:26px;border:1px solid #aaa;border-radius:13px;font-size:7.5px;color:#777;text-align:center;line-height:24px}

/* footer */
.site-footer{left:0;top:970px;width:668px;height:230px;background:var(--footer)}
.footer-title{top:30px;color:#fff;font-size:11.5px;font-weight:500}
.cat-list{top:58px;list-style:none;font-size:7px;color:var(--footer-text)}
.cat-list li{height:15.4px;display:flex;gap:9px}
.cat-list li::before{content:"♫";color:var(--pink);font-size:7px}
.contact{left:478px;width:160px;font-size:7px;color:var(--footer-text);display:flex;align-items:center;gap:9px}
.contact .ico{width:17px;height:17px;border:1.5px solid var(--pink);border-radius:50%;display:flex;align-items:center;justify-content:center;flex:none}
.contact em{font-style:normal;color:var(--pink);font-size:8.5px}
.social{top:162px;width:24px;height:24px;border-radius:50%;background:#2f2f2f}
</style>
</head>
<body>

<header class="abs site-header">
  <div class="abs brand"><span class="name">VELORA</span><span class="sub">MUSIC</span></div>
  <div class="abs search-field">Search text here...</div>
  <div class="abs search-btn">SEARCH</div>
  <div class="abs filters">
    <span><i class="radio on"></i>All</span>
    <span><i class="radio"></i>Song</span>
    <span><i class="radio"></i>Artist</span>
  </div>
</header>

<section class="abs hero" role="img" aria-label="Photo of a smiling young woman with curly hair wearing headphones, in an orange top against a grey-blue wall">
  <svg class="abs hero-arrow" style="left:34px" width="14" height="34" viewBox="0 0 14 34"><path d="M12 1 L2 17 L12 33" fill="none" stroke="#fff" stroke-width="1.5"/></svg>
  <svg class="abs hero-arrow" style="left:621px" width="14" height="34" viewBox="0 0 14 34"><path d="M2 1 L12 17 L2 33" fill="none" stroke="#fff" stroke-width="1.5"/></svg>
  <div class="abs hero-caption">Enjoying the music beats</div>
</section>

<section class="abs features">
  <div class="abs feature" style="left:42px">
    <div class="badge pink">
      <svg width="30" height="30" viewBox="0 0 30 30" fill="#fff"><path d="M12 3h6v9h5l-8 8-8-8h5z"/><path d="M3 18h6l3 3h6l3-3h6v9H3z"/></svg>
    </div>
    <h3>DOWNLOAD<b>MUSIC</b></h3>
    <p>Lorem ipsum dolor sit amet conse ctetur adipising elit, sed do eiusmod tempor incididunt ut labore et dolore magna aliqua. Ut enim ad.</p>
    <span class="pill pink">READ MORE</span>
  </div>
  <div class="abs feature" style="left:246px">
    <div class="badge blue">
      <svg width="32" height="32" viewBox="0 0 24 24"><path d="M12 2.5l2.9 6 6.6.8-4.9 4.5 1.3 6.5L12 17l-5.9 3.3 1.3-6.5-4.9-4.5 6.6-.8z" fill="none" stroke="#fff" stroke-width="1.6" stroke-linejoin="round"/></svg>
    </div>
    <h3>RATE YOUR<b>FAVOURITE ONE</b></h3>
    <p>Lorem ipsum dolor sit amet conse ctetur adipising elit, sed do eiusmod tempor incididunt ut labore et dolore magna aliqua. Ut enim ad.</p>
    <span class="pill blue">READ MORE</span>
  </div>
  <div class="abs feature" style="left:449px">
    <div class="badge orange">
      <svg width="30" height="30" viewBox="0 0 30 30" fill="#fff"><path d="M11 6l15-3v17a4 4 0 1 1-2.5-3.7V8.5L13.5 10.5V23a4 4 0 1 1-2.5-3.7z"/></svg>
    </div>
    <h3>FREE AND<b>EASY</b></h3>
    <p>Lorem ipsum dolor sit amet conse ctetur adipising elit, sed do eiusmod tempor incididunt ut labore et dolore magna aliqua. Ut enim ad.</p>
    <span class="pill orange">READ MORE</span>
  </div>
</section>

<h2 class="abs popular-title"><b>POPULAR</b> MUSIC</h2>
<nav class="abs tabs">
  <span class="active">RnB</span><span class="sep">\</span><span>Hip hop</span><span class="sep">\</span><span>Rock</span><span class="sep">\</span><span>Afro-pop</span>
</nav>

<article class="abs card" style="left:42px;top:699px">
  <div class="abs cover" role="img" aria-label="RnB album cover" style="background:linear-gradient(135deg,#2a2a2a,#0c0c0c)"></div>
  <h4 class="abs">MUSIC TITLE <span class="stars">★★★★☆</span></h4>
  <p class="abs">sed do eiusmod situd tempor incididunt ut labore et.</p>
  <div class="abs dl"><svg width="7" height="7" viewBox="0 0 10 10" fill="#fff"><path d="M4 0h2v4h2L5 7 2 4h2zM0 8h10v2H0z"/></svg>DOWNLOAD</div>
</article>
<article class="abs card" style="left:242px;top:699px">
  <div class="abs cover" role="img" aria-label="RnB album cover with a city skyline" style="background:linear-gradient(180deg,#3fb3d8,#1e5f8a)"></div>
  <h4 class="abs">MUSIC TITLE <span class="stars">★★★★☆</span></h4>
  <p class="abs">sed do eiusmod situd tempor incididunt ut labore et.</p>
  <div class="abs dl"><svg width="7" height="7" viewBox="0 0 10 10" fill="#fff"><path d="M4 0h2v4h2L5 7 2 4h2zM0 8h10v2H0z"/></svg>DOWNLOAD</div>
</article>
<article class="abs card" style="left:442px;top:699px">
  <div class="abs cover" role="img" aria-label="Red RnB album cover" style="background:radial-gradient(circle,#b8142a,#3a0508)"></div>
  <h4 class="abs">MUSIC TITLE <span class="stars">★★★★☆</span></h4>
  <p class="abs">sed do eiusmod situd tempor incididunt ut labore et.</p>
  <div class="abs dl"><svg width="7" height="7" viewBox="0 0 10 10" fill="#fff"><path d="M4 0h2v4h2L5 7 2 4h2zM0 8h10v2H0z"/></svg>DOWNLOAD</div>
</article>
<article class="abs card" style="left:42px;top:796px">
  <div class="abs cover" role="img" aria-label="Blue club classics album cover" style="background:linear-gradient(180deg,#2c6f9c,#0b2438)"></div>
  <h4 class="abs">MUSIC TITLE <span class="stars">★★★★☆</span></h4>
  <p class="abs">sed do eiusmod situd tempor incididunt ut labore et.</p>
  <div class="abs dl"><svg width="7" height="7" viewBox="0 0 10 10" fill="#fff"><path d="M4 0h2v4h2L5 7 2 4h2zM0 8h10v2H0z"/></svg>DOWNLOAD</div>
</article>
<article class="abs card" style="left:242px;top:796px">
  <div class="abs cover" role="img" aria-label="Album cover with a singer portrait" style="background:linear-gradient(135deg,#d9c6b4,#5a4030)"></div>
  <h4 class="abs">MUSIC TITLE <span class="stars">★★★★☆</span></h4>
  <p class="abs">sed do eiusmod situd tempor incididunt ut labore et.</p>
  <div class="abs dl"><svg width="7" height="7" viewBox="0 0 10 10" fill="#fff"><path d="M4 0h2v4h2L5 7 2 4h2zM0 8h10v2H0z"/></svg>DOWNLOAD</div>
</article>
<article class="abs card" style="left:442px;top:796px">
  <div class="abs cover" role="img" aria-label="Purple R&amp;B mix album cover" style="background:linear-gradient(180deg,#8a2c9c,#2a0f3a)"></div>
  <h4 class="abs">MUSIC TITLE <span class="stars">★★★★☆</span></h4>
  <p class="abs">sed do eiusmod situd tempor incididunt ut labore et.</p>
  <div class="abs dl"><svg width="7" height="7" viewBox="0 0 10 10" fill="#fff"><path d="M4 0h2v4h2L5 7 2 4h2zM0 8h10v2H0z"/></svg>DOWNLOAD</div>
</article>

<div class="abs view-all">VIEW ALL SONG LIST</div>

<footer class="abs site-footer">
  <h3 class="abs footer-title" style="left:42px">CATEGORIES</h3>
  <ul class="abs cat-list" style="left:42px">
    <li>All Categories</li><li>Pop</li><li>Rap/Hip Hop</li><li>Rock</li><li>R&amp;B</li><li>Latin</li><li>Country</li><li>Electronica/Dance</li><li>Alternative/Indie</li>
  </ul>
  <ul class="abs cat-list" style="left:186px">
    <li>Reggae/Ska</li><li>Comedy</li><li>Folk</li><li>Blues</li><li>Jazz</li><li>World</li><li>Christian &amp; Gospel</li><li>Classical</li><li>Political</li>
  </ul>
  <ul class="abs cat-list" style="left:331px">
    <li>Sound Effects</li><li>Names</li><li>Sports</li><li>Holiday</li><li>Nature</li><li>Area Codes</li><li>Alerts &amp; Alarms</li><li>TV/Movie</li>
  </ul>

  <h3 class="abs footer-title" style="left:478px">CONTACT INFO</h3>
  <div class="abs contact" style="top:55px">
    <span class="ico"><svg width="8" height="9" viewBox="0 0 10 12"><path d="M5 11S1 6.5 1 4.2A4 4 0 0 1 9 4.2C9 6.5 5 11 5 11z" fill="none" stroke="#e0136d" stroke-width="1.3"/><circle cx="5" cy="4.3" r="1.3" fill="#e0136d"/></svg></span>
    <span>27 Orchard Lane, Brookfield,<br>WI 53005</span>
  </div>
  <div class="abs contact" style="top:83px">
    <span class="ico"><svg width="8" height="8" viewBox="0 0 10 10"><path d="M2 1l2 2-1 1.5c.7 1.3 1.2 1.8 2.5 2.5L7 6l2 2-1.5 1.5C4 9 1 6 .5 2.5z" fill="#e0136d"/></svg></span>
    <span>Tel: <em>555-014-2230</em></span>
  </div>
  <div class="abs contact" style="top:104px">
    <span class="ico"><svg width="8" height="8" viewBox="0 0 10 10" fill="#e0136d"><rect x="2.5" y="0.5" width="5" height="3"/><rect x="0.5" y="4" width="9" height="5" rx="1"/></svg></span>
    <span>Fax: <em>555-014-2230</em></span>
  </div>
  <div class="abs contact" style="top:127px">
    <span class="ico"><svg width="8" height="7" viewBox="0 0 10 8"><rect x="0.5" y="0.5" width="9" height="7" fill="#e0136d"/><path d="M0.5 0.5L5 4.5 9.5 0.5" fill="none" stroke="#1c1c1c" stroke-width="1"/></svg></span>
    <span>Email: <em>info@veloramusic.com</em></span>
  </div>
  <div class="abs social" style="left:478px"></div>
  <div class="abs social" style="left:505px"></div>
  <div class="abs social" style="left:532px"></div>
</footer>

</body>
</html>
```